Investment company needing business card

We are wanting a business card which looks sharp and easy on the eye. We are thinking of having a business card with the logo embossed on it, to really make it stand out. We will only have a small amount of information of the business card, person's name, position, email address and phone number

Contact Information for Business Card

Danielle Frost
Executive Assistant
+64 21 473 5162
danielf@harwickpartners.co.nz

Requirements
Must have
• Embossed logo
Should not have
• Not to be busy

```html
<!DOCTYPE html>
<html lang="en">
<head>
<meta charset="utf-8">
<title>Harwick Partners – Business Card</title>
<link rel="stylesheet" href="https://fonts.googleapis.com/css2?family=Lato:wght@400;700;900&display=swap">
<style>
  :root {
    --green: #25c08f;
    --green-light: #2ed3a0;
    --grey: #7d7f80;
    --white: #ffffff;
    --paper: #f7f7f6;
    --backdrop: #e6e4df;
  }
  html, body {
    margin: 0;
    padding: 0;
    width: 1200px;
    height: 780px;
    overflow: hidden;
    background: var(--backdrop);
    font-family: "Lato", sans-serif;
  }
  .card {
    position: absolute;
    left: 100px;
    top: 104px;
    width: 1000px;
    height: 572px;
    border-radius: 30px;
    overflow: hidden;
    background: var(--paper);
    box-shadow: 0 12px 30px rgba(0,0,0,0.18);
  }
  .card-waves {
    position: absolute;
    inset: 0;
    width: 100%;
    height: 100%;
  }
  .wave-grey { fill: var(--grey); }
  .wave-green { fill: url(#greenFill); stroke: var(--white); stroke-width: 8; }

  .brand {
    position: absolute;
    left: 70px;
    top: 140px;
    display: flex;
    align-items: center;
    gap: 18px;
  }
  .brand-mark {
    width: 40px;
    height: 40px;
    background: var(--green);
  }
  .brand-name {
    font-weight: 900;
    font-size: 38px;
    letter-spacing: 1px;
    color: var(--green);
    text-transform: uppercase;
  }
  .brand-rule {
    position: absolute;
    left: 128px;
    top: 206px;
    width: 330px;
    height: 2px;
    background: var(--grey);
  }

  .contact {
    position: absolute;
    left: 520px;
    top: 388px;
    color: var(--white);
  }
  .contact-name {
    margin: 0;
    font-weight: 700;
    font-size: 28px;
    line-height: 1.1;
  }
  .contact-role {
    margin: 2px 0 22px;
    font-weight: 400;
    font-size: 21px;
  }
  .contact-line {
    display: flex;
    align-items: center;
    gap: 12px;
    font-size: 22px;
    margin: 6px 0;
  }
  .contact-icon {
    width: 24px;
    height: 24px;
    flex: none;
  }
</style>
</head>
<body>
  <div class="card">
    <svg class="card-waves" viewBox="0 0 1000 572" preserveAspectRatio="none" aria-hidden="true">
      <defs>
        <linearGradient id="greenFill" x1="0" y1="1" x2="1" y2="0">
          <stop offset="0" stop-color="#2ed3a0"/>
          <stop offset="1" stop-color="#1fb383"/>
        </linearGradient>
      </defs>
      <path class="wave-grey" d="M230 572 C390 460 440 320 510 220 S600 20 625 0 L1000 0 L1000 572 Z"/>
      <path class="wave-green" d="M275 580 C420 470 480 330 560 230 S700 20 770 -6 L1010 -6 L1010 580 Z"/>
    </svg>

    <div class="brand">
      <div class="brand-mark"></div>
      <div class="brand-name">Harwick Partners</div>
    </div>
    <div class="brand-rule"></div>

    <div class="contact">
      <p class="contact-name">Danielle Frost</p>
      <p class="contact-role">Executive Assistant</p>
      <div class="contact-line">
        <svg class="contact-icon" viewBox="0 0 24 24" aria-hidden="true">
          <rect x="1" y="1" width="22" height="22" rx="3" fill="none" stroke="#fff" stroke-width="2"/>
          <path d="M8 6 L10 6 L11 9 L9.5 10.5 C10.3 12 11.8 13.6 13.5 14.5 L15 13 L18 14 L18 16 C18 17 17 18 16 18 C10 17.5 6.5 14 6 8 C6 7 7 6 8 6 Z" fill="#fff"/>
        </svg>
        <span>+64 21 473 5162</span>
      </div>
      <div class="contact-line">
        <svg class="contact-icon" viewBox="0 0 24 24" aria-hidden="true">
          <rect x="1" y="1" width="22" height="22" rx="3" fill="none" stroke="#fff" stroke-width="2"/>
          <rect x="5" y="7" width="14" height="10" fill="none" stroke="#fff" stroke-width="1.8"/>
          <path d="M5 7 L12 13 L19 7" fill="none" stroke="#fff" stroke-width="1.8"/>
        </svg>
        <span>danielf@harwickpartners.co.nz</span>
      </div>
    </div>
  </div>
</body>
</html>
```